Looking for a cool & simple business-card-design for digital agency

Hi!

We are a web agency that offers Reputation Management, Vextor & Seo Services and software development. We like cool things, we like innovative styles.

We have uploaded our logo.

Project Deadline Extended Reason: Client does not want any designs with the colorful logo. Please send us submissions ONLY with the blac and white logo. What the client would like to see:1) Back of the card: is a silver logo on a black background2) front of the card with all the data, please use white background and black logo thank you Added Friday, May 8, 2015

Industry/Entity Type

Software

```html
<!DOCTYPE html>
<html lang="en">
<head>
<meta charset="utf-8">
<title>NetMerit Business Card</title>
<link rel="stylesheet" href="https://fonts.googleapis.com/css2?family=Jost:wght@300;400;500;700&display=swap">
<style>
  :root {
    --backdrop: #e3e4e6;
    --card-white: #ffffff;
    --card-black: #232323;
    --ink: #1c1c1c;
    --ink-soft: #555555;
    --silver: #d2d2d2;
  }
  * { box-sizing: border-box; margin: 0; padding: 0; }
  html, body {
    width: 1200px;
    height: 1000px;
    overflow: hidden;
    background: var(--backdrop);
    font-family: "Jost", sans-serif;
  }
  .stage {
    position: relative;
    width: 1200px;
    height: 1000px;
  }
  .card {
    position: absolute;
    left: 280px;
    width: 640px;
    height: 366px;
    border-radius: 3px;
    box-shadow: 0 10px 28px rgba(0, 0, 0, 0.12);
  }
  .card--back {
    top: 80px;
    background: var(--card-black);
  }
  .card--front {
    top: 534px;
    background: var(--card-white);
  }

  /* Wordmark: invented name beside one plain square */
  .wordmark {
    position: absolute;
    display: flex;
    align-items: center;
    gap: 12px;
  }
  .wordmark__square {
    width: 28px;
    height: 28px;
  }
  .wordmark__name {
    font-weight: 700;
    font-size: 40px;
    line-height: 1;
    letter-spacing: 0.5px;
  }
  .card--back .wordmark {
    left: 50%;
    top: 50%;
    transform: translate(-50%, -50%);
  }
  .card--back .wordmark__square { background: var(--silver); }
  .card--back .wordmark__name { color: var(--silver); }

  .card--front .wordmark {
    right: 44px;
    top: 64px;
  }
  .card--front .wordmark__square { background: var(--ink); }
  .card--front .wordmark__name { color: var(--ink); }

  /* Contact block */
  .contact {
    position: absolute;
    left: 44px;
    bottom: 48px;
    color: var(--ink);
  }
  .contact__name {
    font-weight: 700;
    font-size: 17px;
    letter-spacing: 0.5px;
    text-transform: uppercase;
  }
  .contact__role {
    font-weight: 300;
    font-style: italic;
    font-size: 13px;
    color: var(--ink-soft);
    margin-bottom: 16px;
  }
  .contact__line {
    font-weight: 300;
    font-size: 13px;
    line-height: 1.6;
  }
  .contact__label { font-weight: 700; }
</style>
</head>
<body>
<main class="stage">
  <section class="card card--back" aria-label="Card back">
    <div class="wordmark">
      <span class="wordmark__square"></span>
      <span class="wordmark__name">NetMerit</span>
    </div>
  </section>

  <section class="card card--front" aria-label="Card front">
    <div class="wordmark">
      <span class="wordmark__square"></span>
      <span class="wordmark__name">NetMerit</span>
    </div>
    <div class="contact">
      <p class="contact__name">Jordan Hale</p>
      <p class="contact__role">Managing Director</p>
      <p class="contact__line">18 Harbor Lane, Fairview, CA 90210</p>
      <p class="contact__line"><span class="contact__label">Tel:</span> +61 800-555-0142 · <span class="contact__label">E-mail:</span> info@netmerit.com</p>
    </div>
  </section>
</main>
</body>
</html>
```